Upmarket Dessert Lounge needs a Business Card Design

We are an upmarket dessert lounge needing a business card to match our image.

We want something that is simple yet beautiful, feminine, classy, sophisticated and elegant. We want it to stand out and don't mind if it is bold.

The design should include our logo and colours of red or maroon with gold highlights. We don't mind if black is used.

Marlow & Quince

Target Market(s)

For those who like to indulge or treat themselves and give in to their temptations on good quality desserts.

Industry/Entity Type

Business

Requirements
Must have
• Must include our logo and our name

Marlow & Quince

M & Q

```html
<!DOCTYPE html>
<html lang="en">
<head>
<meta charset="utf-8">
<title>Marlow &amp; Quince – Business Card</title>
<link rel="stylesheet" href="https://fonts.googleapis.com/css2?family=Source+Sans+3:wght@400;600;700&display=swap">
<style>
  :root {
    --backdrop: #9a6b48;
    --card: #ffffff;
    --maroon: #7a1416;
    --blush: #d9b3ab;
    --ink: #3a3a3a;
    --shadow: rgba(0, 0, 0, 0.35);
  }
  * { margin: 0; padding: 0; box-sizing: border-box; }
  html, body {
    width: 1200px;
    height: 402px;
    overflow: hidden;
    background: var(--backdrop);
    font-family: "Source Sans 3", Arial, sans-serif;
  }
  .stage { position: relative; width: 1200px; height: 402px; }
  .card {
    position: absolute;
    top: 57px;
    width: 512px;
    height: 293px;
    background: var(--card);
    box-shadow: 0 3px 10px var(--shadow);
  }
  .card--front { left: 63px; }
  .card--back { left: 630px; }

  .brand-name {
    position: absolute;
    left: 28px;
    top: 68px;
    width: 200px;
    text-align: center;
    color: var(--maroon);
    font-weight: 600;
    font-size: 21px;
    letter-spacing: 1px;
  }
  .address {
    position: absolute;
    right: 252px;
    top: 170px;
    text-align: right;
    color: var(--maroon);
    font-size: 12.5px;
    line-height: 15px;
  }
  .contact-list {
    position: absolute;
    right: 252px;
    top: 213px;
    list-style: none;
    color: var(--ink);
    font-size: 12.5px;
  }
  .contact-list li {
    display: flex;
    align-items: center;
    justify-content: flex-end;
    gap: 6px;
    height: 17.5px;
  }
  .contact-list svg { width: 10px; height: 10px; fill: var(--ink); }

  .monogram-faint {
    position: absolute;
    left: 330px;
    top: 162px;
    width: 150px;
    text-align: center;
    color: var(--blush);
    font-weight: 600;
    font-size: 40px;
  }
  .person {
    position: absolute;
    left: 336px;
    top: 262px;
    color: var(--maroon);
    font-size: 16px;
    font-weight: 700;
  }
  .person .title { font-weight: 400; font-size: 13px; }

  .monogram-large {
    position: absolute;
    left: 0;
    top: 0;
    width: 100%;
    height: 100%;
    display: flex;
    align-items: center;
    justify-content: center;
    color: var(--maroon);
    font-weight: 600;
    font-size: 84px;
  }
</style>
</head>
<body>
<main class="stage">
  <section class="card card--front">
    <div class="brand-name">MARLOW &amp; QUINCE</div>

    <address class="address">
      Street Name, City Name<br>State Zip Code
    </address>

    <ul class="contact-list">
      <li>987-654-3210
        <svg viewBox="0 0 10 10" aria-hidden="true"><path d="M2 0.5 L3.6 2.6 L2.7 3.6 Q4 6 6.4 7.3 L7.4 6.4 L9.5 8 L8.3 9.5 Q4.5 9.3 2 6.8 Q-0.2 4 0.5 1.8 Z"/></svg>
      </li>
      <li>987-654-3210
        <svg viewBox="0 0 10 10" aria-hidden="true"><path d="M2.5 0 H7.5 V10 H2.5 Z M3.3 1.2 V6.5 H6.7 V1.2 Z M4.4 7.7 H5.6 V8.8 H4.4 Z" fill-rule="evenodd"/></svg>
      </li>
      <li>info@marlowquince.com
        <svg viewBox="0 0 10 10" aria-hidden="true"><path d="M0 2 H10 V8 H0 Z"/><path d="M0.4 2.4 L5 5.6 L9.6 2.4" stroke="#fff" stroke-width="0.8" fill="none"/></svg>
      </li>
      <li>www.marlowquince.com
        <svg viewBox="0 0 10 10" aria-hidden="true"><circle cx="5" cy="5" r="4.5"/><path d="M0.5 5 H9.5 M5 0.5 V9.5 M5 0.5 Q2 5 5 9.5 M5 0.5 Q8 5 5 9.5" stroke="#fff" stroke-width="0.7" fill="none"/></svg>
      </li>
    </ul>

    <div class="monogram-faint">M &amp; Q</div>

    <p class="person">Your name, <span class="title">Title</span></p>
  </section>

  <section class="card card--back">
    <div class="monogram-large">M &amp; Q</div>
  </section>
</main>
</body>
</html>
```